Bright and beautiful business card for a coach

I'm a personal and business coach based in Perth, Australia. I need a business card that whilst subtle and elegant, will stand out and appeal on a table full of cards.

My business name is Fern Mentoring and the business card must represent the warmth and brightness implied in the name, without being gimmicky. It must have a warmth and appeal and be easy to read.

I prefer clean, minimalist designs.

It must align with the feel of my website and socials: https://www.fernmentoring-example.com.au/
https://www.instagram.com/fernmentoringau/
https://www.facebook.com/fernmentoringau
Updates

Hi Designers Thank you so much for taking the time to submit designs. I wonder if I could have explained myself a little better. Most of the designs that have been submitted look rather formal and many have quite corporate looking embellishments on them (to my eye). I would like softer, warmer, more organic. I’m open to people playing about and being more abstract, using softer embellishments (e.g the line drawing flowers and grasses I’ve used in my socials) incorporating other colours from my palette or like the social icons in my email signature (in PDF), perhaps playing with size/oversize, playing with the bleed. Please don’t be constrained by what I’ve already done, it merely needs to compliment. I’m sorry if I’m not using the right words or have led you astray. I’m no designer, but I’ve done my website, socials, email signature etc all myself (my logo was a design contest) and I was really hoping for my business card to be something more creative than I could have made with a template. Reminder: No black cards/sides please. Thank you 😊

Target Market(s)

Individuals, most likely but not all female. Creative thinkers. Likely professionals.

Industry/Entity Type

Business & Personal Coach

Contact Information for Business Card

(Fern Mentoring Logo) Name: Greta Pellham; Title: Business & Personal Coach; Phone number: +61 (0)458 913307; Email: greta@fernmentoring-example.com.au; Website: https://fernmentoring-example.com.au; Social icons for Facebook, Instagram & LinkedIn: @fernmentoringAU. Optional strapline: "A thinking partner to help you cut through the noise"

Font styles to use
Sans Serif

Colors
00AB8E
00BBA5
67D7C9
C6EFE9
E9F9F6
59FF00
82FF00
B8FF75
E3FFCB
F4FFEA
FFC000
F8CF3A
FAE287
FDF2CF
FEFAEE

Requirements
Must have
• Must align with feel of my website and socials. Must have a pop of #FFC000 (possibly whole of one side, or at least a block). Bright or white background. Easy to read.
Nice to have
• Possibly incorporate the sunshine/grass picture I have used in website and socials - will upload.
Should not have
• Must not be black or dark. Not impersonal or corporate looking.

```html
<!DOCTYPE html>
<html lang="en">
<head>
<meta charset="utf-8">
<title>Fern Mentoring – Business Card</title>
<link rel="stylesheet" href="https://fonts.googleapis.com/css2?family=Lato:wght@400;700&family=Sacramento&display=swap">
<style>
  :root {
    --backdrop: #e4e4e4;
    --paper: #ffffff;
    --gold-top: #f6c41c;
    --gold-mid: #e29d0c;
    --amber-bottom: #c36a14;
    --ink-light: #ffffff;
    --logo-amber: #e3a00c;
    --card-shadow: rgba(0, 0, 0, 0.18);
  }
  * { box-sizing: border-box; margin: 0; padding: 0; }
  html, body { width: 1200px; height: 900px; overflow: hidden; }
  body {
    background: var(--backdrop);
    font-family: "Lato", sans-serif;
  }
  .canvas {
    width: 1200px; height: 900px;
    display: flex; align-items: center; justify-content: center; gap: 80px;
  }
  .card {
    width: 340px; height: 580px;
    position: relative; overflow: hidden;
    box-shadow: 0 12px 30px var(--card-shadow);
  }

  /* Front side */
  .card-front {
    background: var(--paper);
    display: flex; flex-direction: column; align-items: center; justify-content: center; gap: 26px;
  }
  .brand-disc {
    width: 200px; height: 200px; border-radius: 50%;
    background: linear-gradient(180deg, var(--gold-top), var(--logo-amber) 55%, var(--amber-bottom));
  }
  .brand-name {
    font-family: "Lato", sans-serif; font-weight: 700;
    font-size: 22px; letter-spacing: 4px; text-transform: uppercase;
    color: var(--logo-amber);
  }

  /* Back side */
  .card-back {
    background: linear-gradient(180deg, var(--gold-top) 0%, var(--gold-mid) 45%, var(--amber-bottom) 100%);
    color: var(--ink-light);
  }
  .contact-block {
    position: absolute; top: 34px; right: 26px; width: 230px;
  }
  .person-name {
    font-family: "Sacramento", cursive; font-size: 44px; line-height: 1;
    text-align: right;
  }
  .person-title {
    font-size: 12px; text-align: right; margin-top: 4px;
    padding-bottom: 8px; border-bottom: 1px solid var(--ink-light);
  }
  .contact-list { list-style: none; margin-top: 8px; font-size: 11.5px; line-height: 1.7; }
  .contact-list li { display: flex; align-items: center; gap: 6px; white-space: nowrap; }
  .contact-list svg { width: 10px; height: 10px; flex: none; }

  .ray-burst {
    position: absolute; left: -40px; top: 190px; width: 200px; height: 240px;
    border-radius: 0 50% 50% 0;
    background: radial-gradient(circle at 0% 50%, rgba(255,255,255,0.55), rgba(255,255,255,0) 70%);
  }

  .strapline {
    position: absolute; top: 232px; right: 34px; width: 170px;
    font-family: "Sacramento", cursive; font-size: 34px; line-height: 1.05;
    text-align: center;
  }
  .strapline span { display: block; }

  .social-handle {
    position: absolute; bottom: 34px; left: 0; right: 0;
    text-align: center; font-size: 15px; letter-spacing: 0.3px;
  }
</style>
</head>
<body>
<main class="canvas">
  <section class="card card-front" aria-label="Card front">
    <div class="brand-disc" aria-hidden="true"></div>
    <p class="brand-name">Fern Mentoring</p>
  </section>

  <section class="card card-back" aria-label="Card back">
    <div class="contact-block">
      <h1 class="person-name">Greta Pellham</h1>
      <p class="person-title">Business &amp; Personal Coach</p>
      <ul class="contact-list">
        <li>
          <svg viewBox="0 0 10 10"><path d="M2 1 L4 1 L4.6 3 L3.5 3.8 Q4.6 5.9 6.2 6.5 L7 5.4 L9 6 L9 8 Q8.5 9 7.5 9 Q1 8 1 2.5 Q1 1.5 2 1 Z" fill="#fff"/></svg>
          +61 (0)458 913307
        </li>
        <li>
          <svg viewBox="0 0 10 10"><rect x="0.5" y="2" width="9" height="6" fill="#fff"/><path d="M0.5 2 L5 5.5 L9.5 2" stroke="#e29d0c" stroke-width="0.9" fill="none"/></svg>
          greta@fernmentoring-example.com.au
        </li>
        <li>
          <svg viewBox="0 0 10 10"><circle cx="5" cy="5" r="4.2" stroke="#fff" stroke-width="1" fill="none"/><ellipse cx="5" cy="5" rx="1.8" ry="4.2" stroke="#fff" stroke-width="0.8" fill="none"/><line x1="0.8" y1="5" x2="9.2" y2="5" stroke="#fff" stroke-width="0.8"/></svg>
          fernmentoring-example.com.au
        </li>
      </ul>
    </div>

    <div class="ray-burst" role="img" aria-label="Decorative sun-ray lines radiating from the left edge"></div>

    <p class="strapline">
      <span>A</span>
      <span>thinking partner</span>
      <span>to</span>
      <span>help you</span>
      <span>cut through</span>
      <span>the noise</span>
    </p>

    <p class="social-handle">@fernmentoringAU</p>
  </section>
</main>
</body>
</html>
```